Brightway Haus Inc. Business Card Design

Brightway Haus Inc. is in search of a great clean design for our business cards!

Looking to incorporate our full logo and watermark on side one (however, I am open to having the text and watermark separated within the design.)

On side two, I am looking to have contact information (Name, Position, Phone #, Email, Website (www.thebrightwayhaus.ca). Can have the logo and/or watermark as part of the design if applicable.

Please add tagline "Where Shine Counts" on either side 1 or 2. This tagline can be in a sans serif, serif or cursive font as long as it compliments overall design. Capitalization can be title or sentence case depending on how it fits within the design.

Get creative!! Looking for a clean, crisp, premium design! Looking for a glossy card finish with spot UV features when printed. Cards will also be printed with rounded corners. Standard dimensions (3.5 x 2).

Target Market(s)

B2B - primary clients are business owners or property management corporations. (residential jobs are few and far between)

Industry/Entity Type

Business

Contact Information for Business Card

- clean, crisp design
- double sided
- spot UV accents and glossy finish upon printing
- standard business card size (3.5 x 2) with rounded corners
- please see project description for requirements per side

Font styles to use
Sans Serif

Requirements
Must have
• - adequate bleeds with print ready files
• - cohesive design elements between side 1 & 2
• - spot UV elements (can be on both sides or just one, use your discretion)
• - colour pallet should match the logo file provided
• - incorporate tagline "where shine counts" (this tagline can be in a serif or sans serif font as long as it is complimentary to the overall design.
Nice to have
• - Premium elements with a clean design
Should not have
• - Please omit cartoon or whimsical like designs, think premium.
• - Colours should not stray from the pallet of the provided logo.

```html
<!DOCTYPE html>
<html lang="en">
<head>
<meta charset="utf-8">
<title>Brightway Haus Inc. Business Card</title>
<link rel="stylesheet" href="https://fonts.googleapis.com/css2?family=Open+Sans:wght@700;800&family=Roboto:wght@400;500&display=swap">
<style>
  :root {
    --teal: #0a9da0;
    --teal-deep: #08898c;
    --navy: #1b1f4b;
    --paper: #f4f4f4;
    --white: #ffffff;
    --backdrop: #e6e6e6;
  }
  * { margin: 0; padding: 0; box-sizing: border-box; }
  html, body { width: 1200px; height: 576px; overflow: hidden; }
  body {
    background: var(--backdrop);
    position: relative;
    font-family: "Roboto", Arial, sans-serif;
  }
  .card {
    position: absolute;
    top: 138px;
    width: 484px;
    height: 294px;
    border-radius: 14px;
    overflow: hidden;
  }
  .card--front {
    left: 81px;
    background: linear-gradient(135deg, var(--teal) 0%, var(--teal-deep) 100%);
  }
  .card--back { left: 602px; background: var(--teal); }

  .front-logo {
    position: absolute;
    left: 0; right: 0; top: 124px;
    display: flex; align-items: center; justify-content: center; gap: 10px;
  }
  .front-logo__mark { width: 30px; height: 30px; background: var(--navy); }
  .front-logo__name {
    font-family: "Open Sans", Arial, sans-serif;
    font-weight: 800;
    font-size: 32px;
    letter-spacing: -0.5px;
    color: var(--white);
    line-height: 1;
  }

  .back-shape { position: absolute; inset: 0; }

  .contact { position: absolute; left: 21px; color: var(--white); }
  .contact__name { top: 34px; font-size: 22px; font-weight: 500; }
  .contact__role { top: 66px; font-size: 12.5px; }
  .contact__address { top: 184px; font-size: 13px; line-height: 17px; }
  .contact__list { top: 222px; list-style: none; font-size: 13px; }
  .contact__list li { display: flex; align-items: center; gap: 10px; height: 18.5px; }
  .contact__list svg { width: 11px; height: 11px; fill: var(--white); }

  .side-brand {
    position: absolute;
    top: 30px;
    left: 400px;
    height: 240px;
    display: flex;
    gap: 4px;
    writing-mode: vertical-rl;
    transform: rotate(180deg);
    justify-content: center;
  }
  .side-brand__name {
    font-family: "Open Sans", Arial, sans-serif;
    font-weight: 800;
    font-size: 25px;
    letter-spacing: -0.3px;
    color: var(--teal);
    line-height: 1;
  }
  .side-brand__tagline {
    font-size: 13px;
    letter-spacing: 2.6px;
    color: var(--navy);
    line-height: 1;
    order: -1;
  }
</style>
</head>
<body>
  <section class="card card--front" aria-label="Card front">
    <div class="front-logo">
      <span class="front-logo__mark"></span>
      <span class="front-logo__name">BRIGHTWAY HAUS INC.</span>
    </div>
  </section>

  <section class="card card--back" aria-label="Card back">
    <svg class="back-shape" viewBox="0 0 484 294" aria-hidden="true">
      <path d="M308 0 C262 80 254 200 318 294 L484 294 L484 0 Z" fill="var(--paper)"/>
      <path d="M290 52 C258 130 270 230 330 294 L318 294 C262 220 256 130 290 52 Z" fill="var(--navy)"/>
    </svg>

    <h1 class="contact contact__name">Daniel Reyes</h1>
    <p class="contact contact__role">Managing Director</p>
    <p class="contact contact__address">48 Harbour Lane<br>Suite 210, Halifax NS</p>
    <ul class="contact contact__list">
      <li><svg viewBox="0 0 12 12"><path d="M1 3c0-1 1-2 2-2h6c1 0 2 1 2 2v1H8V3H4v1H1zM2 5h8l1 6H1z"/></svg>1800-555-0142</li>
      <li><svg viewBox="0 0 12 12"><path d="M0 2h12v1L6 7 0 3zM0 4.5l6 4 6-4V10H0z"/></svg>daniel@thebrightwayhaus.ca</li>
      <li><svg viewBox="0 0 12 12"><path d="M6 0a6 6 0 100 12A6 6 0 006 0zm0 1.3c.6.7 1 1.9 1.2 3.2H4.8C5 3.2 5.4 2 6 1.3zM1.4 5.5h2.3v1H1.4zm6.9 0h2.3v1H8.3zM4.8 7.5h2.4C7 8.8 6.6 10 6 10.7 5.4 10 5 8.8 4.8 7.5z"/></svg>www.thebrightwayhaus.ca</li>
    </ul>

    <div class="side-brand">
      <span class="side-brand__name">BRIGHTWAY HAUS INC.</span>
      <span class="side-brand__tagline">Where Shine Counts</span>
    </div>
  </section>
</body>
</html>
```